Commercial Loan Originator Business Card (CHANGE COLORS SCHEME)

CHANGE COLOR SCHEME - SAME DESIGN

Name Marlene Agate
Title Commercial Loan Originator
Office (800) 417-2906 x68
Direct (240) 615-2043
Email freshgreens4life@quillbox.example

Name Dale Morrow
Office (800) 417-2906 x70
Direct (410) 392-5184
Email d.morthehomeguy@quillbox.example

Name Leonard Vasko
Office (800) 417-2906 x71
Direct (215) 463-0712
Email l.vasko41@quillbox.example

Name Gwen Halsey
Office (800) 417-2906 x
Direct (202) 548-1370
Email ghalsey63@quillbox.example

Name Mirna Ashby
Office (800) 417-2906 x72
Direct (240) 871-4526
Email tristatehomelending@quillbox.example

```html
<!DOCTYPE html>
<html lang="en">
<head>
<meta charset="utf-8">
<title>Gwen Halsey – Commercial Loan Originator</title>
<link rel="stylesheet" href="https://fonts.googleapis.com/css2?family=Cinzel:wght@600&family=Poppins:wght@400&display=swap">
<style>
  :root {
    --page-bg: #e9eaec;
    --card-bg: #ffffff;
    --brand-main: #0f6b5c;
    --brand-light: #cfe6df;
    --ink: #222222;
    --photo-top: #e7e3ea;
    --photo-mid: #6b4a86;
    --photo-deep: #2a2d4a;
  }
  * { margin: 0; padding: 0; box-sizing: border-box; }
  html, body {
    width: 1200px; height: 952px; overflow: hidden;
    background: var(--page-bg);
  }
  .business-card {
    position: absolute; left: 71px; top: 148px;
    width: 1058px; height: 655px;
    background: var(--card-bg);
    overflow: hidden;
    box-shadow: 0 6px 18px rgba(0,0,0,0.18);
  }
  .corner-accent { position: absolute; left: 0; top: 0; width: 1058px; height: 180px; }
  .bottom-band {
    position: absolute; left: 0; bottom: 0; width: 100%; height: 17px;
    background: var(--brand-main);
  }
  .portrait-area {
    position: absolute; left: 585px; top: 72px; width: 473px; height: 566px;
    border-radius: 200px 200px 0 0;
    background: radial-gradient(ellipse at 60% 28%, var(--photo-top) 0%, #c9b7c9 28%, var(--photo-mid) 60%, var(--photo-deep) 100%);
    opacity: 0.9;
  }
  .identity { position: absolute; left: 46px; top: 336px; }
  .person-name {
    font-family: "Cinzel", "Times New Roman", serif;
    font-weight: 600; font-size: 46px; line-height: 1;
    color: var(--brand-main); letter-spacing: 0.5px;
  }
  .person-title {
    font-family: "Poppins", Arial, sans-serif;
    font-size: 30px; line-height: 1.1; color: var(--ink); margin-top: 2px;
  }
  .contact-list {
    position: absolute; left: 48px; top: 468px; list-style: none;
    font-family: "Poppins", Arial, sans-serif; font-size: 31px; color: var(--ink);
  }
  .contact-item { display: flex; align-items: center; height: 38px; white-space: nowrap; }
  .contact-icon { width: 32px; height: 30px; margin-right: 14px; flex: none; }
  .contact-label { color: var(--brand-main); margin-left: 10px; }
</style>
</head>
<body>
  <main class="business-card">
    <svg class="corner-accent" viewBox="0 0 1058 180" aria-hidden="true">
      <polygon points="0,102 665,0 0,171" fill="var(--brand-light)"/>
      <polygon points="0,0 665,0 0,102" fill="var(--brand-main)"/>
    </svg>

    <div class="portrait-area" role="img" aria-label="Portrait photo of Gwen Halsey smiling and gesturing with an open hand"></div>

    <section class="identity">
      <h1 class="person-name">GWEN HALSEY</h1>
      <p class="person-title">Commercial Loan Originator</p>
    </section>

    <ul class="contact-list">
      <li class="contact-item">
        <svg class="contact-icon" viewBox="0 0 32 30" aria-hidden="true">
          <path d="M7 4 L11 4 L13 10 L10 12 Q12 18 18 21 L20 18 L26 20 L26 24 Q24 28 20 27 Q8 23 4 10 Q4 5 7 4 Z" fill="none" stroke="var(--brand-main)" stroke-width="2.6" stroke-linejoin="round"/>
          <path d="M17 3 Q26 4 28 13" fill="none" stroke="var(--brand-main)" stroke-width="2.4" stroke-linecap="round"/>
          <path d="M17 8 Q22 9 23 14" fill="none" stroke="var(--brand-main)" stroke-width="2.4" stroke-linecap="round"/>
        </svg>
        <span>(800) 417-2906 x</span>
      </li>
      <li class="contact-item">
        <svg class="contact-icon" viewBox="0 0 32 30" aria-hidden="true">
          <path d="M7 4 L11 4 L13 10 L10 12 Q12 18 18 21 L20 18 L26 20 L26 24 Q24 28 20 27 Q8 23 4 10 Q4 5 7 4 Z" fill="none" stroke="var(--brand-main)" stroke-width="2.6" stroke-linejoin="round"/>
          <path d="M17 3 Q26 4 28 13" fill="none" stroke="var(--brand-main)" stroke-width="2.4" stroke-linecap="round"/>
          <path d="M17 8 Q22 9 23 14" fill="none" stroke="var(--brand-main)" stroke-width="2.4" stroke-linecap="round"/>
        </svg>
        <span>(202) 548-1370</span><span class="contact-label">(Direct )</span>
      </li>
      <li class="contact-item">
        <svg class="contact-icon" viewBox="0 0 32 30" aria-hidden="true">
          <rect x="1" y="7" width="30" height="19" fill="var(--brand-main)"/>
          <path d="M1 7 L16 18 L31 7" fill="none" stroke="#ffffff" stroke-width="2"/>
          <path d="M1 26 L12 16 M31 26 L20 16" fill="none" stroke="#ffffff" stroke-width="1.5"/>
        </svg>
        <span>ghalsey63@quillbox.example</span>
      </li>
    </ul>

    <div class="bottom-band"></div>
  </main>
</body>
</html>
```